Business Cards for a law firm

Business cards for our law firm. Use our silhoette logo and OAK PARTNERS - check our website (www.oakpartners.example)

Contact Information for Business Card

our silhouette logo, OAK PARTNERS, 800-555-0147, Dorian Pemberton, dorian@oakpartners.example

Requirements
Must have
• our silhouette logo, OAK PARTNERS, 800-555-0147, Dorian Pemberton, dorian@oakpartners.example

```html
<!DOCTYPE html>
<html lang="en">
<head>
<meta charset="utf-8">
<title>Oak Partners – Business Cards</title>
<link rel="stylesheet" href="https://fonts.googleapis.com/css2?family=Montserrat:wght@400;600&family=Lato:wght@400&family=Lora:wght@400&display=swap">
<style>
  :root {
    --backdrop: #2a2c31;
    --navy: #3d4f72;
    --navy-deep: #2c3a58;
    --gold: #f8b733;
    --white: #ffffff;
    --photo-light: #e9e9ec;
    --photo-dark: #2b3046;
  }
  * { box-sizing: border-box; margin: 0; padding: 0; }
  html, body {
    width: 1200px; height: 985px; overflow: hidden;
    background: var(--backdrop);
  }
  .card {
    position: absolute;
    width: 540px; height: 309px;
    border-radius: 18px;
    overflow: hidden;
    box-shadow: 0 10px 30px rgba(0,0,0,.35);
  }
  .card-front { left: 40px; top: 338px; background: var(--white); }
  .card-back  { left: 620px; top: 338px; background: var(--navy); }
  .card-shapes { position: absolute; inset: 0; }

  .brand {
    position: absolute;
    display: flex; align-items: center; gap: 12px;
    font-family: "Montserrat", sans-serif;
    font-weight: 600;
    color: var(--white);
    letter-spacing: 2px;
    line-height: 1;
  }
  .brand-mark {
    width: 30px; height: 30px; border-radius: 50%;
    background: var(--white); flex: none;
  }
  .card-front .brand { left: 206px; top: 72px; font-size: 27px; }
  .card-front .brand-name span { display: block; }
  .card-front .brand-name span + span { margin-top: 6px; }

  .name-tag {
    position: absolute; left: 228px; top: 152px;
    font-family: "Montserrat", sans-serif; font-weight: 400;
    font-size: 18px; letter-spacing: 1px;
    color: var(--navy); text-transform: uppercase;
  }
  .contact-list {
    position: absolute; left: 208px; top: 196px;
    list-style: none;
    font-family: "Lato", sans-serif; font-size: 14px; color: var(--white);
  }
  .contact-list li { display: flex; align-items: center; gap: 8px; height: 22px; }
  .contact-icon { width: 15px; height: 15px; flex: none; }
  .website {
    position: absolute;
    font-family: "Lora", serif;
    letter-spacing: 3px;
  }
  .card-front .website { left: 208px; top: 252px; font-size: 14px; color: var(--gold); }

  .card-back .brand { left: 0; right: 0; top: 120px; justify-content: center; font-size: 30px; }
  .card-back .website {
    left: 0; right: 0; top: 190px; text-align: center;
    font-size: 13px; letter-spacing: 5px; color: var(--white);
  }
</style>
</head>
<body>

<section class="card card-front" aria-label="Business card front">
  <svg class="card-shapes" width="540" height="309" viewBox="0 0 540 309">
    <defs>
      <linearGradient id="portrait-tone" x1="0" y1="0" x2="0" y2="1">
        <stop offset="0" stop-color="var(--photo-light)"/>
        <stop offset="0.35" stop-color="var(--photo-dark)"/>
        <stop offset="1" stop-color="var(--photo-dark)"/>
      </linearGradient>
    </defs>
    <polygon class="accent-top" points="225,55 300,0 540,0 540,55" fill="var(--gold)"/>
    <rect class="accent-bottom" x="170" y="290" width="370" height="19" fill="var(--gold)"/>
    <polygon class="info-panel" points="170,290 170,110 225,55 540,55 540,290" fill="var(--navy)"/>
    <polygon class="name-ribbon" points="190,168 206,150 540,150 540,186 206,186" fill="var(--gold)"/>
    <rect role="img" aria-label="Portrait photo of Dorian Pemberton in a dark suit" x="0" y="40" width="186" height="269" fill="url(#portrait-tone)"/>
  </svg>

  <div class="brand">
    <span class="brand-mark"></span>
    <span class="brand-name"><span>OAK</span><span>PARTNERS</span></span>
  </div>

  <p class="name-tag">Dorian Pemberton</p>

  <ul class="contact-list">
    <li>
      <svg class="contact-icon" viewBox="0 0 16 16"><circle cx="8" cy="8" r="8" fill="var(--gold)"/><path d="M5.2 4.2l1.4-.3.9 2-1 .8a6 6 0 0 0 2.8 2.8l.8-1 2 .9-.3 1.4c-3.6.4-7-3-6.6-6.6z" fill="var(--navy)"/></svg>
      <span>800-555-0147</span>
    </li>
    <li>
      <svg class="contact-icon" viewBox="0 0 16 16"><circle cx="8" cy="8" r="8" fill="var(--gold)"/><rect x="4" y="5.2" width="8" height="5.6" fill="none" stroke="var(--navy)" stroke-width="1.1"/><path d="M4 5.4l4 3 4-3" fill="none" stroke="var(--navy)" stroke-width="1.1"/></svg>
      <span>dorian@oakpartners.example</span>
    </li>
  </ul>

  <p class="website">www.oakpartners.example</p>
</section>

<section class="card card-back" aria-label="Business card back">
  <div class="brand">
    <span class="brand-mark"></span>
    <span class="brand-name">OAK PARTNERS</span>
  </div>
  <p class="website">www.oakpartners.example</p>
</section>

</body>
</html>
```